Website design for Silver Harbor Trading Inc

We are looking to build a website for our company. We are a scrap metal recycling company based out of Los Angeles. We purchase scrap metal in the US and ship them to China for recycling into fresh metal ores to supply industrial users. We would designs that emphasize the color green given our name and the nature of our business. Recycling themes are welcomed. We already have a URL at:
http://silverharbortradinginc.example/
At this point, I would like 4 pages:
- Home page
- About Us
- Resources
- Contact us
Our sister company is Maple Crest Intl Inc and they have a website that we can use as a starting point.
http://www.maplecrest-intl.example/
Our competitor has a website below. However we dislike the design given we believe it looks rather dull.
http://www.orientalloysalvage.example/en/
Lastly, this is for a website shell only. Please design the template, graphics, and color schemes. We will write the contents later.

```html
<!DOCTYPE html>
<html lang="en">
<head>
<meta charset="utf-8">
<title>Silver Harbor Trading Inc</title>
<link href="https://fonts.googleapis.com/css2?family=Source+Sans+3:ital,wght@0,400;0,600;0,700;1,600&family=Oswald:wght@400;500&display=swap" rel="stylesheet">
<style>
  :root {
    --navy: #00233a;
    --band: #0a3f5f;
    --red: #c40000;
    --blue: #2587c3;
    --heading-blue: #1f84c0;
    --green: #3fb457;
    --green-light: #7fd38a;
    --white: #ffffff;
    --text-grey: #666a6e;
    --label-dark: rgba(25, 25, 25, 0.88);
  }
  * { margin: 0; padding: 0; box-sizing: border-box; }
  html, body { width: 1200px; height: 756px; overflow: hidden; }
  body {
    background: var(--navy);
    font-family: "Source Sans 3", Arial, sans-serif;
    color: var(--white);
    position: relative;
  }
  .feature-band {
    position: absolute; left: 0; top: 129px; width: 1200px; height: 371px;
    background: var(--band);
  }
  .page { position: absolute; left: 181px; top: 0; width: 840px; height: 756px; }

  .brand {
    position: absolute; left: 4px; top: 44px;
    display: flex; align-items: center; gap: 10px;
  }
  .brand-mark { width: 30px; height: 30px; background: var(--green); }
  .brand-name { font-size: 23px; font-weight: 700; color: var(--white); letter-spacing: -0.5px; }

  .main-nav { position: absolute; left: 0; top: 95px; display: flex; gap: 2px; }
  .main-nav a {
    display: block; width: 144px; height: 29px; line-height: 29px; text-align: center;
    background: var(--blue); color: var(--white); text-decoration: none;
    font-size: 12.5px; font-weight: 600; text-transform: uppercase;
  }
  .main-nav a.is-current { background: var(--red); }

  .follow { position: absolute; left: 644px; top: 90px; display: flex; align-items: center; gap: 4px; }
  .follow-label { font-family: "Oswald", sans-serif; font-size: 14px; margin-right: 6px; }
  .follow-dot { width: 26px; height: 26px; border-radius: 50%; }
  .dot-1 { background: #2c6fb6; } .dot-2 { background: #3aa6e0; } .dot-3 { background: #2a7fa8; } .dot-4 { background: #f0a21e; }

  .hero {
    position: absolute; left: 0; top: 129px; width: 580px; height: 371px;
    background: linear-gradient(160deg, #c7ccd2 0%, #6d7c8a 30%, #3b4d5e 55%, #0f1a26 100%);
  }
  .hero-title {
    position: absolute; left: 30px; top: 236px; width: 520px;
    font-weight: 700; letter-spacing: -2px; color: var(--white); line-height: 0.9;
  }
  .hero-title .line { display: block; white-space: nowrap; }
  .hero-title .small { font-size: 42px; }
  .hero-title .accent { font-size: 60px; color: var(--green-light); }
  .hero-title .large { font-size: 60px; }
  .hero-arrows { position: absolute; right: 6px; bottom: 6px; display: flex; gap: 2px; }
  .hero-arrows span { width: 23px; height: 23px; background: #ee0000; display: flex; align-items: center; justify-content: center; }

  .side { position: absolute; left: 584px; top: 129px; width: 256px; }
  .tile { position: relative; height: 101px; margin-bottom: 1px; }
  .tile-photo { position: absolute; inset: 0 0 26px 0; }
  .photo-ship { background: linear-gradient(135deg, #dfe6ee, #5a6e8a 60%, #2a3d5c); }
  .photo-pipes { background: linear-gradient(135deg, #6b4a3a, #2a1e18 60%, #8c6a55); }
  .tile-label {
    position: absolute; left: 0; bottom: 0; width: 100%; height: 26px;
    background: var(--label-dark); display: flex; align-items: center; justify-content: space-between;
    padding: 0 8px 0 12px; font-family: "Oswald", sans-serif; font-size: 14px; text-transform: uppercase;
  }
  .photo-touch { height: 94px; background: linear-gradient(90deg, #3a3a3a, #c9ccd0 45%, #5a5d62); }
  .tracking { height: 74px; background: var(--red); padding: 10px 12px; }
  .tracking h3 { font-family: "Oswald", sans-serif; font-weight: 400; font-size: 14px; text-transform: uppercase; }
  .tracking p { font-size: 9.5px; font-style: italic; font-weight: 600; margin: 2px 0 0 5px; }
  .tracking-options { display: flex; gap: 20px; margin-top: 8px; font-size: 10.5px; }
  .tracking-options label { display: flex; align-items: center; gap: 4px; }
  .radio { width: 10px; height: 10px; border-radius: 50%; background: linear-gradient(#f4f4f4, #aaa); }

  .welcome {
    position: absolute; left: 0; top: 505px; width: 840px; height: 165px;
    background: var(--white); padding: 20px 22px;
  }
  .welcome h1 { font-size: 16.5px; font-weight: 600; color: var(--heading-blue); text-transform: uppercase; }
  .welcome .lead { color: var(--red); font-size: 11.5px; line-height: 17px; margin-top: 8px; width: 760px; }
  .welcome .body-copy { color: var(--text-grey); font-size: 9.5px; line-height: 15.5px; margin-top: 9px; }

  .footer-nav { position: absolute; left: 4px; top: 689px; display: flex; font-size: 8.5px; font-weight: 600; }
  .footer-nav a { color: var(--white); text-decoration: none; text-transform: uppercase; }
  .footer-nav .sep { margin: 0 17px; }
  .copyright { position: absolute; left: 4px; top: 711px; font-size: 8.5px; font-weight: 600; text-transform: uppercase; }
  .address { position: absolute; left: 517px; top: 686px; font-size: 8.5px; font-weight: 600; text-transform: uppercase; white-space: nowrap; }
  .contacts { position: absolute; left: 517px; top: 707px; display: flex; gap: 22px; font-size: 9.5px; font-weight: 600; white-space: nowrap; }
  .contacts span { display: flex; align-items: center; gap: 5px; white-space: nowrap; }
  .contacts svg { flex: none; }
</style>
</head>
<body>
  <div class="feature-band"></div>
  <div class="page">
    <header>
      <div class="brand">
        <span class="brand-mark"></span>
        <span class="brand-name">Silver Harbor Trading</span>
      </div>
      <nav class="main-nav">
        <a href="#" class="is-current">Home</a>
        <a href="#">About Us</a>
        <a href="#">Resources</a>
        <a href="#">Contact Us</a>
      </nav>
      <div class="follow">
        <span class="follow-label">FOLLOW US :</span>
        <span class="follow-dot dot-1"></span>
        <span class="follow-dot dot-2"></span>
        <span class="follow-dot dot-3"></span>
        <span class="follow-dot dot-4"></span>
      </div>
    </header>

    <section class="hero" role="img" aria-label="Container ship loaded with cargo sailing across open sea">
      <div class="hero-title">
        <span class="line"><span class="small">Silver</span> <span class="accent">Harbor</span></span>
        <span class="line large">Trading</span>
      </div>
      <div class="hero-arrows">
        <span><svg width="8" height="10" viewBox="0 0 8 10"><path d="M6 1 L2 5 L6 9 Z" fill="#fff"/></svg></span>
        <span><svg width="8" height="10" viewBox="0 0 8 10"><path d="M2 1 L6 5 L2 9 Z" fill="#fff"/></svg></span>
      </div>
    </section>

    <aside class="side">
      <div class="tile">
        <div class="tile-photo photo-ship" role="img" aria-label="Container ship seen from above"></div>
        <div class="tile-label">Quick Cargo Tracking
          <svg width="8" height="10" viewBox="0 0 8 10"><path d="M1 1 L5 5 L1 9 M3 1 L7 5 L3 9" stroke="#fff" fill="none" stroke-width="1.2"/></svg>
        </div>
      </div>
      <div class="tile">
        <div class="tile-photo photo-pipes" role="img" aria-label="Stacked steel pipes ready for recycling"></div>
        <div class="tile-label">Recycling into Fresh Metal
          <svg width="8" height="10" viewBox="0 0 8 10"><path d="M1 1 L5 5 L1 9 M3 1 L7 5 L3 9" stroke="#fff" fill="none" stroke-width="1.2"/></svg>
        </div>
      </div>
      <div class="photo-touch" role="img" aria-label="Hand touching a digital tracking interface"></div>
      <div class="tracking">
        <h3>MC Tracking</h3>
        <p>we strongly believe in being an honest</p>
        <div class="tracking-options">
          <label><span class="radio"></span>B/L</label>
          <label><span class="radio"></span>BKG</label>
          <label><span class="radio"></span>CNTR</label>
        </div>
      </div>
    </aside>

    <main class="welcome">
      <h1>Welcome to Silver Harbor Trading</h1>
      <p class="lead">We are a scrap metal recycling company based out of Los Angeles. We purchase scrap metal in the US and ship them to China for recycling into fresh metal ores to supply industrial users</p>
      <p class="body-copy">Lorem Ipsum is that it has a more-or-less normal distribution of letters, as opposed to using 'Content here, content here', making it look like readable English. Many desktop publishing packages and web page editors now use Lorem Ipsum as their default model text, and a search for 'lorem ipsum' will uncover many web sites still in their infancy. Various versions have evolved over the years, sometimes by accident, sometimes on purpose&nbsp; Lorem Ipsum is that it has a more-or-less normal distribution of letters...</p>
    </main>

    <footer>
      <nav class="footer-nav">
        <a href="#">Home</a><span class="sep">|</span>
        <a href="#">About Us</a><span class="sep">|</span>
        <a href="#">Resources</a><span class="sep">|</span>
        <a href="#">Contact Us</a>
      </nav>
      <p class="copyright">Copyright © 2013. Silver Harbor Trading. All rights reserved.</p>
      <p class="address">4520 Dockside Ave. # 118, Harbor City, CA 90710</p>
      <div class="contacts">
        <span><svg width="11" height="11" viewBox="0 0 11 11"><path d="M2 1 L4 1 L5 3.5 L3.8 4.6 Q5 7 6.5 7.2 L7.5 6 L10 7 L10 9 Q9.5 10 8 10 Q1 9 1 2 Q1 1 2 1 Z" fill="#fff"/></svg>(555) 240-1187</span>
        <span><svg width="11" height="11" viewBox="0 0 11 11"><rect x="3" y="1" width="5" height="3" fill="#fff"/><rect x="1" y="4" width="9" height="4" fill="#fff"/><rect x="3" y="7" width="5" height="3" fill="#fff" stroke="#00233a" stroke-width="0.8"/></svg>(555) 240-1190</span>
        <span><svg width="12" height="9" viewBox="0 0 12 9"><rect x="0.5" y="0.5" width="11" height="8" fill="#fff"/><path d="M0.5 0.5 L6 5 L11.5 0.5" stroke="#00233a" fill="none"/></svg>info@silverharbor.example</span>
      </div>
    </footer>
  </div>
</body>
</html>
```